Card Design Project

A simple, funky, cool birth announcement card
Not corporate, but arty
Not childish nor girlish
No baby pictures

Text is tbc (eg name and date may change)

Front side: just the name "fenna"
Should be easy to read

Back side text (in Dutch):

We vinden je nu al leuk!

20 JUNE 2013
Singapore

Dochter van Marieke Dorrel & Joost Vermalen

Yangon, Myanmar
+95 1 64 8319
Chat: Marieke.Dorrel
Chat: Joost.Vermalen

Size will be A6
Updates

Reason: Dear designers, At this stage we would like to have one or more designers to draft up the card (of which the final text is still tbd as the baby is yet to be born) using the typeface used on the left below (or similar!) of the newly added picture - in black - in fluorescent colours Can you get back to us in a few days? Thanks

Target Market(s)

Our funky friends in holland.

Industry/Entity Type

Baby

Requirements
Must have
• Colours, aswe are very happy to welcome this baby.
Something that makes it stand out from all other baby birth announcement cards

A6 size
Deadline 21 June
Printing will be on white (thick paper 250g)
Design for 5mm "bleedsides" all around
At least available in PDF (and other formats)
Nice to have
• We've recently moved from netherlands to Yangon
We could include the iconic kyauktaran pagoda

I would like for it to look like a cool party announcement

Include bright fluoriscent colours, including orange.
The enveloppe will be orange
Should not have
• Any baby stuff, soft pink dominance, childish stuff.

```html
<!DOCTYPE html>
<html lang="nl">
<head>
<meta charset="utf-8">
<title>Geboortekaart – achterkant</title>
<link rel="stylesheet" href="https://fonts.googleapis.com/css2?family=Indie+Flower&family=Barlow:wght@400;600;700&display=swap">
<style>
  :root {
    --ink-pink: #f0145a;
    --ink-cyan: #5de6f3;
    --ink-dark: #3a3a3a;
    --ink-orange: #f05a14;
    --ink-green: #8fd14a;
    --paper: #ffffff;
    --bar-orange: #ff5a00;
    --bar-yellow: #f2ee00;
    --bar-green: #7cf07a;
    --bar-cyan: #55e8ff;
  }
  * { margin: 0; padding: 0; box-sizing: border-box; }
  html, body {
    width: 1200px;
    height: 799px;
    overflow: hidden;
    background: var(--paper);
  }
  .card {
    position: relative;
    width: 1200px;
    height: 799px;
    overflow: hidden;
    background: var(--paper);
    font-family: "Barlow", "Helvetica Neue", Arial, sans-serif;
    color: var(--ink-dark);
  }
  .headline {
    position: absolute;
    left: 0;
    top: 62px;
    width: 100%;
    text-align: center;
    font-family: "Indie Flower", cursive;
    font-weight: 400;
    font-size: 212px;
    line-height: 200px;
    color: var(--ink-pink);
    transform: scaleX(0.7);
    transform-origin: 50% 0;
  }
  .spectrum-bar {
    position: absolute;
    left: 0;
    top: 504px;
    width: 100%;
    height: 8px;
    background: linear-gradient(90deg, var(--bar-orange) 0%, var(--bar-yellow) 40%, var(--bar-green) 72%, var(--bar-cyan) 100%);
  }
  .birth-date {
    position: absolute;
    left: 142px;
    top: 606px;
    width: 440px;
    text-align: center;
  }
  .birth-date__day {
    display: block;
    font-weight: 700;
    font-size: 57px;
    line-height: 60px;
    letter-spacing: 1px;
    color: var(--ink-cyan);
  }
  .birth-date__place {
    display: block;
    font-size: 23px;
    line-height: 30px;
    color: var(--ink-dark);
  }
  .parents {
    position: absolute;
    left: 677px;
    top: 550px;
  }
  .parents__title {
    font-weight: 700;
    font-size: 28px;
    line-height: 34px;
    letter-spacing: 0.3px;
  }
  .parents__address {
    margin-top: 16px;
    font-size: 23px;
    line-height: 30px;
  }
  .parents__divider { color: var(--ink-green); padding: 0 4px; }
  .contact {
    margin-top: 20px;
    font-size: 23px;
    line-height: 34px;
  }
  .contact__label {
    font-size: 14px;
    text-transform: uppercase;
    color: var(--ink-orange);
    letter-spacing: 0.3px;
  }
</style>
</head>
<body>
  <main class="card">
    <h1 class="headline">We vinden je<br>nu al leuk!</h1>

    <div class="spectrum-bar" aria-hidden="true"></div>

    <p class="birth-date">
      <span class="birth-date__day">20 JUNE 2013</span>
      <span class="birth-date__place">Singapore</span>
    </p>

    <section class="parents">
      <h2 class="parents__title">Dochter van Marieke Dorrel<br>&amp; Joost Vermalen</h2>
      <p class="parents__address">Yangon, Myanmar<span class="parents__divider">|</span>+95 1 64 8319</p>
      <p class="contact">
        <span class="contact__label">Chat:</span> Marieke.Dorrel &amp; Joost.Vermalen<br>
        <span class="contact__label">Email:</span> dorrelmarieke@postvak.nl
      </p>
    </section>
  </main>
</body>
</html>
```